Corporate travel agency website design

Hello I need a website design that will look professional. I want that anyone that gos on our site understands that we are a large successful company. I want it to be up to par with other large companies. The site should be sleek and neat.
Below I will attach my logo. A recent one page add I made and content for my add that will be used for the website.

```html
<!DOCTYPE html>
<html lang="en">
<head>
<meta charset="utf-8">
<title>Meridian Travel – Business Travel Management</title>
<link href="https://fonts.googleapis.com/css2?family=Poppins:wght@300;400;500;600;700;800&display=swap" rel="stylesheet">
<style>
:root{
  --navy:#0b1a36;
  --navy-deep:#06101f;
  --ink:#111a2b;
  --text:#3b4250;
  --sky:#dcf3f9;
  --sky-btn:#c9ecf8;
  --white:#ffffff;
  --footer:#020409;
  --line:#c7ccd4;
}
*{margin:0;padding:0;box-sizing:border-box}
html,body{width:1200px;height:4535px;overflow:hidden}
body{position:relative;font-family:'Poppins',sans-serif;color:var(--ink);background:var(--white)}
.abs{position:absolute}

/* header */
.brand-block{left:100px;top:0;width:270px;height:66px;background:var(--navy);display:flex;align-items:center;justify-content:center;gap:10px}
.brand-block .dot{width:12px;height:12px;border-radius:50%;background:var(--sky-btn)}
.brand-block .name{color:var(--white);font-size:15px;font-weight:400;letter-spacing:3px}
.nav{left:370px;top:0;width:725px;height:66px;background:var(--white);display:flex;align-items:center;justify-content:center;gap:38px;font-size:14px;color:var(--ink)}
.nav svg{margin-left:4px}

/* hero */
.hero-photo{left:0;top:0;width:1200px;height:632px;background:linear-gradient(180deg,#1a2a55 0%,#2c3f72 30%,#5a5f86 48%,#b7776a 62%,#d58a58 67%,#3a3440 76%,#1c1f2a 100%)}
.hero-cut{left:0;top:0}
.hero-title{left:0;top:408px;width:1200px;text-align:center;color:var(--white);font-size:50px;font-weight:800;letter-spacing:0.5px}
.btn-start{left:533px;top:483px;width:134px;height:38px;border-radius:19px;background:var(--sky-btn);color:var(--navy);font-size:14px;font-weight:600;display:flex;align-items:center;justify-content:center}

/* why */
.why{left:114px;top:712px;width:972px;text-align:center}
.why h2{font-size:27px;font-weight:700;color:var(--navy-deep);margin-bottom:18px}
.why .lead{font-size:13.5px;font-weight:600;line-height:22px;color:var(--ink);margin-bottom:6px}
.why p{font-size:13.5px;line-height:28px;color:var(--text)}

/* services */
.services{left:0;top:1019px;width:1200px;height:1531px;background:var(--sky)}
.section-title{width:1200px;text-align:center;font-size:27px;font-weight:700;color:var(--navy-deep)}
.svc-photo{border-radius:10px}
.svc-text h3{font-size:22px;font-weight:600;color:var(--ink);line-height:32px;margin-bottom:14px}
.svc-text p{font-size:11.5px;line-height:21px;color:var(--text);text-align:justify}

/* features */
.feature{width:236px;height:268px}
.feature svg.hex{position:absolute;left:0;top:0}
.feature .icon{position:absolute;left:78px;top:48px;width:80px;height:80px}
.feature .label{position:absolute;left:0;top:156px;width:236px;text-align:center;font-size:18px;font-weight:500;line-height:26px;color:var(--ink)}
.feature .go{position:absolute;left:96px;top:226px;width:44px;height:30px}

/* contact */
.contact{left:0;top:3247px;width:1200px;height:713px;background:linear-gradient(180deg,#e4f5fa 0%,#d3eef7 55%,#c6e6f2 100%)}
.card{left:104px;top:3402px;width:991px;height:537px;background:var(--white)}
.info{top:3492px;height:30px;display:flex;align-items:center;gap:10px;font-size:13px;color:var(--ink)}
.info .ic{width:26px;height:26px;border-radius:50%;background:var(--navy);display:flex;align-items:center;justify-content:center}
.sep{top:3484px;width:1px;height:40px;background:#9aa1ac}
.field{font-size:13px}
.field .lbl{font-weight:600;color:var(--ink);margin-bottom:6px}
.field .val{font-size:11px;color:var(--text);padding-bottom:6px;border-bottom:1px solid var(--line)}
.btn-submit{left:540px;top:3836px;width:102px;height:36px;border-radius:18px;background:var(--navy);color:var(--white);font-size:13px;font-weight:600;display:flex;align-items:center;justify-content:center}

/* footer */
.footer{left:0;top:3960px;width:1200px;height:575px;background:var(--footer)}
.mail-title{left:0;top:4016px;width:1200px;text-align:center;color:var(--white);font-size:28px;font-weight:600}
.mail-sub{left:0;top:4068px;width:1200px;text-align:center;color:var(--white);font-size:14px}
.subscribe{left:260px;top:4106px;width:664px;height:44px;border-radius:22px;background:var(--white);display:flex;align-items:center;justify-content:space-between;padding:0 4px 0 22px;font-size:14px;color:var(--ink)}
.subscribe .btn{width:100px;height:36px;border-radius:18px;background:var(--navy);color:var(--white);font-size:13px;font-weight:600;display:flex;align-items:center;justify-content:center}
.rule{left:135px;width:914px;height:1px;background:#3a3f4a}
.foot-brand{left:120px;top:4340px;width:360px;display:flex;align-items:center;justify-content:center;gap:12px;color:var(--white);font-size:28px;font-weight:300;letter-spacing:4px}
.foot-brand .mark{width:16px;height:16px;border-radius:50%;border:2px solid var(--white)}
.col h4{color:var(--white);font-size:17px;font-weight:600;margin-bottom:14px}
.col li{list-style:none;color:var(--white);font-size:14px;line-height:30px}
.social li{display:flex;align-items:center;gap:10px;line-height:42px;font-size:13px}
.social .circ{width:30px;height:30px;border-radius:50%;border:2px solid var(--white)}
.copyright{left:0;top:4490px;width:1200px;text-align:center;color:var(--white);font-size:14px}
</style>
</head>
<body>

<!-- hero -->
<div class="abs hero-photo" role="img" aria-label="Passenger jet taking off over a runway at sunset"></div>
<svg class="abs hero-cut" width="1200" height="640" viewBox="0 0 1200 640" aria-hidden="true">
  <polygon points="0,487 927,632 0,632" fill="#ffffff"/>
  <polygon points="927,632 1200,430 1200,640 0,640 0,632" fill="#ffffff"/>
  <polygon points="880,625 1200,395 1200,430 927,632" fill="#0b1a36"/>
</svg>

<div class="abs brand-block"><span class="dot"></span><span class="name">MERIDIAN TRAVEL</span></div>
<nav class="abs nav">
  <span>Home</span><span>Why Choose Meridian Travel</span><span>Our Services</span><span>Contact Us</span>
  <svg width="14" height="14" viewBox="0 0 14 14"><circle cx="6" cy="6" r="4.5" fill="none" stroke="#111a2b" stroke-width="2"/><line x1="9.5" y1="9.5" x2="13" y2="13" stroke="#111a2b" stroke-width="2.2"/></svg>
</nav>

<h1 class="abs hero-title">WELCOME TO MERIDIAN TRAVEL</h1>
<div class="abs btn-start">Get Started</div>

<!-- why choose -->
<section class="abs why">
  <h2>WHY CHOOSE MERIDIAN TRAVEL?</h2>
  <p class="lead">Meridian Travel is a global leader in business travel management services. We drive savings, efficiency, and unparalleled service to businesses and their travelers all around the world.</p>
  <p>If you are looking for a tailored travel managed solution focused on offering white glove service and fulfilling your individual preferences, while delivering customer excellence, you've come to the right place. At Meridian Travel, our mission is to have you focus on your day to day business while we handle all of the logistics and details for the most successful all encompassing travel experience. From emergency passport arrangements to last minute cancellations, re-bookings, and other intricate travel challenges, Meridian Travel is well versed in handling the routine array of travel services, as well as solving any travel related issue that might arise.</p>
</section>

<!-- services -->
<section class="abs services"></section>
<h2 class="abs section-title" style="left:0;top:1166px">OUR SERVICES</h2>

<div class="abs svc-photo" style="left:218px;top:1250px;width:386px;height:388px;background:linear-gradient(160deg,#c9d8e2,#8ea4b6 55%,#4d5c6e)" role="img" aria-label="Business travellers walking through an airport with luggage"></div>
<div class="abs svc-text" style="left:667px;top:1334px;width:310px">
  <h3>Unparalled Service</h3>
  <p>Meridian Travel is famous for our concierge style approach to travel. From detailed planning, to commercial or private air travel, transportation, including car rentals, chauffeurs, busses for larger groups, hotels, all styles of lodging accomodations, special event planning and more, Meridian Travel is like having your own personal or corporate travel butler.</p>
</div>

<div class="abs svc-text" style="left:204px;top:1672px;width:329px">
  <h3>Budget and Travel Spend Reporting</h3>
  <p>Having a travel management service will ensure that your company enforces corporate compliance and maintains control over travel decisions. This ensures that your employees stick to your budget, which in turn will protect your bottom line. Travel expenses can be costly. Having a savvy and experienced corporate travel manager who can access deep discounts not available to the public will ensure your travel is booked across the board at the lowest prices, expenses are kept under control.</p>
</div>
<div class="abs svc-photo" style="left:597px;top:1628px;width:383px;height:387px;background:linear-gradient(160deg,#8a5a3c,#5b4034 45%,#2a3750 80%,#c9d3de)" role="img" aria-label="Travellers checking in at a hotel reception desk"></div>

<div class="abs svc-photo" style="left:220px;top:2006px;width:385px;height:389px;background:linear-gradient(180deg,#cfe4f3,#8fb6d6 45%,#3f6f9a 70%,#c5dbec)" role="img" aria-label="Silhouetted travellers in an airport terminal with a plane outside"></div>
<div class="abs svc-text" style="left:669px;top:2066px;width:320px">
  <h3>Efficiency</h3>
  <p>Time is your most valuable tool! Our goal at Meridian Travel is to have your employees' complete focus be on your core business, while having us handle all the logistics for their travel. One of the most appreciated services we offer is the management of travel headaches. Unforeseen circumstances such as cancellations, missed flights, cancelled flights, last minute bookings or changed plans, can take hours to rectify. Meridian Travel handles all of these tedious repositionings expeditiously, saving your employees precious time. Give your company a competitive edge by having Meridian Travel handle your team's travel arrangements.</p>
</div>

<!-- features -->
<svg width="0" height="0" style="position:absolute">
  <defs>
    <filter id="soft" x="-20%" y="-20%" width="140%" height="140%"><feDropShadow dx="0" dy="2" stdDeviation="4" flood-color="#9aa6b5" flood-opacity="0.45"/></filter>
    <symbol id="hexShape" viewBox="0 0 236 268"><polygon points="118,8 226,70 226,198 118,260 10,198 10,70" fill="#ffffff" stroke="#eef1f4" stroke-width="2" stroke-linejoin="round" filter="url(#soft)"/></symbol>
    <symbol id="goBtn" viewBox="0 0 44 30"><path d="M0,6 Q22,-6 44,6 L44,8 A22,22 0 0 1 0,8 Z" fill="#0b1a36"/><polyline points="19,9 25,15 19,21" fill="none" stroke="#ffffff" stroke-width="2.4" stroke-linecap="round" stroke-linejoin="round"/></symbol>
  </defs>
</svg>

<div class="abs feature" style="left:142px;top:2656px">
  <svg class="hex" width="236" height="268"><use href="#hexShape"/></svg>
  <svg class="icon" viewBox="0 0 80 80"><g fill="#0b1a36"><rect x="10" y="20" width="10" height="36" rx="5" transform="rotate(-12 15 38)"/><rect x="22" y="10" width="10" height="44" rx="5"/><rect x="34" y="8" width="10" height="46" rx="5"/><rect x="46" y="12" width="10" height="42" rx="5"/><rect x="56" y="24" width="9" height="32" rx="4.5" transform="rotate(25 60 40)"/><path d="M14,48 L66,48 L62,74 L22,74 Z"/></g></svg>
  <div class="label">White Glove<br>Service</div>
  <svg class="go"><use href="#goBtn"/></svg>
</div>

<div class="abs feature" style="left:482px;top:2656px">
  <svg class="hex" width="236" height="268"><use href="#hexShape"/></svg>
  <svg class="icon" viewBox="0 0 80 80"><path d="M12,4 H44 L58,18 V50 H38 V76 H12 Z" fill="#0b1a36"/><g stroke="#ffffff" stroke-width="3"><line x1="20" y1="26" x2="46" y2="26"/><line x1="20" y1="36" x2="46" y2="36"/><line x1="20" y1="46" x2="34" y2="46"/></g><path d="M56,38 L74,44 V58 Q74,70 56,78 Q40,70 40,58 V44 Z" fill="#0b1a36" stroke="#ffffff" stroke-width="2"/><polyline points="48,58 54,64 66,52" fill="none" stroke="#ffffff" stroke-width="3" stroke-linecap="round"/></svg>
  <div class="label">Meridian travel policy<br>compliance</div>
  <svg class="go"><use href="#goBtn"/></svg>
</div>

<div class="abs feature" style="left:822px;top:2656px">
  <svg class="hex" width="236" height="268"><use href="#hexShape"/></svg>
  <svg class="icon" viewBox="0 0 80 80"><g fill="none" stroke="#0b1a36" stroke-width="9" stroke-linecap="round"><path d="M24,20 H56 A12,12 0 0 1 56,44 H24 A12,12 0 0 0 24,68 H56"/></g><g stroke="#0b1a36" stroke-width="3" fill="#0b1a36"><line x1="2" y1="20" x2="14" y2="20"/><polygon points="2,14 8,20 2,26" /><line x1="66" y1="68" x2="76" y2="68"/><polygon points="72,62 78,68 72,74"/></g></svg>
  <div class="label">Streamlined<br>expense reports</div>
  <svg class="go"><use href="#goBtn"/></svg>
</div>

<div class="abs feature" style="left:310px;top:2852px">
  <svg class="hex" width="236" height="268"><use href="#hexShape"/></svg>
  <svg class="icon" viewBox="0 0 80 80"><g fill="#0b1a36"><circle cx="46" cy="10" r="7"/><path d="M40,20 H52 L56,44 L50,46 L54,76 H46 L42,52 L36,76 H28 L36,44 Z"/><rect x="12" y="48" width="16" height="22" rx="3" transform="rotate(-20 20 59)"/></g><line x1="26" y1="48" x2="38" y2="32" stroke="#0b1a36" stroke-width="3"/></svg>
  <div class="label">Full Service travel<br>management</div>
  <svg class="go"><use href="#goBtn"/></svg>
</div>

<div class="abs feature" style="left:653px;top:2852px">
  <svg class="hex" width="236" height="268"><use href="#hexShape"/></svg>
  <svg class="icon" viewBox="0 0 80 80"><g stroke="#0b1a36" stroke-width="3" stroke-linecap="round"><line x1="34" y1="2" x2="34" y2="10"/><line x1="42" y1="0" x2="42" y2="8"/><line x1="50" y1="2" x2="50" y2="10"/></g><circle cx="42" cy="30" r="14" fill="#0b1a36"/><text x="42" y="37" text-anchor="middle" font-family="Poppins,sans-serif" font-size="20" font-weight="700" fill="#ffffff">$</text><path d="M8,52 H16 V74 H8 Z M18,54 Q30,50 44,56 H56 Q60,58 56,62 H40 M18,72 H50 L74,58 Q72,52 66,54 L52,62" fill="#0b1a36" stroke="#0b1a36" stroke-width="3" stroke-linejoin="round"/></svg>
  <div class="label">Unparalled<br>Savings</div>
  <svg class="go"><use href="#goBtn"/></svg>
</div>

<!-- contact -->
<section class="abs contact" role="img" aria-label="Faded airport terminal with aircraft in pale blue"></section>
<h2 class="abs section-title" style="left:0;top:3318px">CONTACT US</h2>
<svg class="abs" style="left:0;top:3880px" width="1200" height="90" viewBox="0 0 1200 90" aria-hidden="true">
  <polygon points="0,80 104,30 104,80" fill="#0b1a36"/>
  <polygon points="1095,20 1200,60 1200,80 1095,80" fill="#0b1a36"/>
</svg>
<div class="abs card"></div>

<div class="abs info" style="left:238px">
  <span class="ic"><svg width="12" height="14" viewBox="0 0 12 14"><path d="M6,0 A5,5 0 0 1 11,5 C11,9 6,14 6,14 C6,14 1,9 1,5 A5,5 0 0 1 6,0 Z" fill="#fff"/><circle cx="6" cy="5" r="2" fill="#0b1a36"/></svg></span>
  <span>50, Lorem ipsum dolor sit</span>
</div>
<div class="abs sep" style="left:461px"></div>
<div class="abs info" style="left:528px">
  <span class="ic"><svg width="14" height="10" viewBox="0 0 14 10"><rect x="0.5" y="0.5" width="13" height="9" fill="#fff"/><polyline points="0.5,0.5 7,6 13.5,0.5" fill="none" stroke="#0b1a36" stroke-width="1.3"/></svg></span>
  <span>info@meridiantravel.com</span>
</div>
<div class="abs sep" style="left:759px"></div>
<div class="abs info" style="left:818px">
  <span class="ic"><svg width="13" height="13" viewBox="0 0 13 13"><path d="M2,0 L5,3 L3.5,5 Q5,8 8,9.5 L10,8 L13,11 L11,13 Q5,13 0,6 Q0,2 2,0 Z" fill="#fff"/></svg></span>
  <span>+1 555 014 2290</span>
</div>

<div class="abs field" style="left:243px;top:3576px;width:294px"><div class="lbl">Name</div><div class="val">| First name</div></div>
<div class="abs field" style="left:634px;top:3576px;width:294px"><div class="lbl">Email Address</div><div class="val">@anymail.com</div></div>
<div class="abs field" style="left:243px;top:3657px;width:294px"><div class="lbl">Phone</div><div class="val">123 456 7890</div></div>
<div class="abs field" style="left:634px;top:3657px;width:294px"><div class="lbl">Subject</div><div class="val">Lorem ipsum</div></div>
<div class="abs field" style="left:243px;top:3746px;width:702px"><div class="lbl">Message</div><div class="val" style="padding-bottom:14px">Lorem ipsum dolor</div></div>
<div class="abs btn-submit">SUBMIT</div>

<!-- footer -->
<footer class="abs footer"></footer>
<svg class="abs" style="left:572px;top:3970px" width="40" height="36" viewBox="0 0 40 36" aria-hidden="true"><g fill="none" stroke="#fff" stroke-width="2"><rect x="2" y="10" width="30" height="22"/><polyline points="2,10 17,22 32,10"/><circle cx="30" cy="10" r="8" fill="#020409"/><polyline points="33,10 27,10 29,7"/></g></svg>
<h2 class="abs mail-title">Join Our Mailing List for News</h2>
<p class="abs mail-sub">Lorem ipsum dolor sit amet, consectetur adipiscing elit, sed do eiusmod tempor</p>
<div class="abs subscribe"><span>Enter Email Address</span><span class="btn">SUBMIT</span></div>
<div class="abs rule" style="top:4189px"></div>

<div class="abs foot-brand"><span class="mark"></span><span>MERIDIAN TRAVEL</span></div>

<div class="abs col" style="left:517px;top:4222px"><h4>USE LINK</h4><ul><li>Home</li><li>About Us</li><li>Our Services</li><li>Contact Us</li></ul></div>
<div class="abs col" style="left:704px;top:4222px"><h4>HELP LINK</h4><ul><li>Terms &amp; Conditions</li><li>Privacy Policy</li><li>Support</li></ul></div>
<div class="abs col social" style="left:915px;top:4222px"><h4>FOLLOW US</h4><ul><li><span class="circ"></span>Chatterly</li><li><span class="circ"></span>Linkwork</li><li><span class="circ"></span>Snapfolio</li><li><span class="circ"></span>Chirpline</li></ul></div>

<div class="abs rule" style="top:4462px"></div>
<p class="abs copyright">2023 © Meridian Travel | All Rights Reserved</p>

</body>
</html>
```